Brivolt Technologies business card design

We need a business card designed with our new logo. it would be great if the card could communicate it is a technology based company.

Target Market(s)

system integrators

Industry/Entity Type

technology, IOT

Contact Information for Business Card

Name, designation, Address, telephone number, email address

Requirements
Must have
• logo and company name
Nice to have
• something to do with technology

```html
<!DOCTYPE html>
<html lang="en">
<head>
<meta charset="utf-8">
<title>Brivolt Technologies – Business Card</title>
<link href="https://fonts.googleapis.com/css2?family=Open+Sans:wght@400;600;700&display=swap" rel="stylesheet">
<style>
  :root {
    --backdrop: #3b3b3b;
    --card: #1b1b1b;
    --card-deep: #141414;
    --accent: #f7931e;
    --ink: #f2f2f2;
    --ink-soft: #d6d6d6;
  }
  * { box-sizing: border-box; margin: 0; padding: 0; }
  html, body {
    width: 1200px; height: 801px; overflow: hidden;
    background: var(--backdrop);
    font-family: "Open Sans", Arial, sans-serif;
  }
  .stage {
    width: 1200px; height: 801px;
    display: flex; align-items: center; justify-content: center; gap: 60px;
  }
  .card {
    position: relative;
    width: 520px; height: 297px;
    background: var(--card);
    border: 2px solid var(--accent);
    overflow: hidden;
  }
  /* brand name block */
  .brand {
    display: flex; align-items: center; gap: 10px;
    color: var(--ink); font-weight: 700; letter-spacing: 1px;
  }
  .brand-mark { width: 18px; height: 18px; background: var(--accent); flex: none; }
  .brand-name { font-size: 20px; line-height: 1.1; text-transform: uppercase; }

  /* front */
  .card-front .brand { position: absolute; left: 34px; top: 110px; }
  .person { position: absolute; right: 34px; top: 36px; text-align: right; }
  .person-name { color: var(--accent); font-weight: 700; font-size: 17px; letter-spacing: .3px; }
  .person-title { color: var(--ink-soft); font-size: 12px; margin-top: 2px; }
  .rule-top { position: absolute; right: 34px; top: 88px; width: 220px; height: 1px; background: var(--accent); }
  .address { position: absolute; right: 34px; top: 104px; text-align: right; color: var(--ink-soft); font-size: 12px; line-height: 1.6; }
  .rule-bottom { position: absolute; left: 34px; bottom: 86px; width: 250px; height: 1px; background: var(--accent); }
  .contact { position: absolute; left: 34px; bottom: 22px; list-style: none; color: var(--ink-soft); font-size: 12px; line-height: 1.7; }
  .contact li { display: flex; align-items: center; gap: 8px; }
  .contact svg { width: 11px; height: 11px; flex: none; }

  /* back */
  .pattern {
    position: absolute; inset: 0;
    background: linear-gradient(135deg, var(--card-deep) 0%, #1e1e1e 55%, #2a2a2a 100%);
  }
  .card-back .brand { position: absolute; right: 34px; bottom: 74px; }
  .card-back .brand-name { font-size: 24px; }
</style>
</head>
<body>
<main class="stage">

  <section class="card card-front" aria-label="Business card front">
    <div class="brand">
      <span class="brand-mark"></span>
      <span class="brand-name">Brivolt Technologies</span>
    </div>

    <div class="person">
      <p class="person-name">DANIEL OKAFOR</p>
      <p class="person-title">President</p>
    </div>
    <div class="rule-top"></div>
    <p class="address">1850 Harbor Crest Dr<br>Seaview CA 92700</p>

    <div class="rule-bottom"></div>
    <ul class="contact">
      <li>
        <svg viewBox="0 0 12 12"><path fill="#f7931e" d="M2.5 1h2l1 3-1.3 1a7 7 0 0 0 2.8 2.8L8 6.5l3 1v2A1.5 1.5 0 0 1 9.5 11 8.5 8.5 0 0 1 1 2.5 1.5 1.5 0 0 1 2.5 1z"/></svg>
        555-014-7782
      </li>
      <li>
        <svg viewBox="0 0 12 12"><rect x="1" y="2.5" width="10" height="7" fill="#f7931e"/><path d="M1 2.5l5 4 5-4" fill="none" stroke="#1b1b1b" stroke-width="1"/></svg>
        info@brivolttechnologies.com
      </li>
      <li>
        <svg viewBox="0 0 12 12"><circle cx="6" cy="6" r="5" fill="#f7931e"/><path d="M1 6h10M6 1c2 2.5 2 7.5 0 10M6 1c-2 2.5-2 7.5 0 10" fill="none" stroke="#1b1b1b" stroke-width=".8"/></svg>
        www.brivolttechnologies.com
      </li>
    </ul>
  </section>

  <section class="card card-back" aria-label="Business card back">
    <div class="pattern" role="img" aria-label="Faint repeating brand-mark decoration in glossy black on black"></div>
    <div class="brand">
      <span class="brand-mark"></span>
      <span class="brand-name">Brivolt Technologies</span>
    </div>
  </section>

</main>
</body>
</html>
```